Design my site www.brieflyledger.com

So here is what I am thinking in terms of design:

https://plenvo.com

https://www.skyluxair.com

http://kalvex.com/harbor-plaza-tower/

I want the theme to be white and blue (royal blue). I attached a paint picture of what I would like the site to look like in terms of placing the text. Generally, what I like about the sites above is that they are simple, you can navigate easily and have some kind of idea of what's going on by looking at the center (picture and motto). Let's establish a clear understanding of how the functional part of the site would look like. Please see the picture attached.

I want to keep it simple: On top would be the Name 'BRIEFLY ledger", somewhere to the right on top on the page would be 'Sign in" button.

In the center would be a picture (maybe a video) with the Motto (on top of it all in capital) OBSERVE NAVIGATE DECIDE and below would be the "sign up now"

Below the picture (like on kalvex.com site) or to the left on top of the page would be "About Us', "Press" "Contact Us' buttons.

Then once the user gets to his page his got 3 tabs " Press Headlines", "Events", " Briefings".

we would keep the same format I only have on the site, but separate for every Tab.

I do not want the user to get distracted. I also want him to be able to access the page though mobile phone and be able to get automatic updates just like Zorvan Pings without having to sign in daily.

The landing page must be minimalist yet with business/corporate feel where users can navigate easily and a "what you see is what you get" approach. You want an image or video (personally I prefer the video.. it does capture the users attention instantly, as long as it is an interesting video), with your taglines in it.

Sections available to public: About Us, Contact Us, Landing Page with Signup Option

Private: Public Sections + User Account Page, Tabs for (Events, Press Headlines, Briefings)

Target Market(s)

PR/media monitoring/diplomatic community

Coding

Coded - Design and coding required

Number of Pages Required

1 page

Font styles to use
Serif
Sans Serif

Colors
0255a3
ec1f27

Requirements
Must have
• a simple landing page, that is user friendly.
Nice to have
• a video with the explanation of how to navigate the site
Should not have
• too many colors, graphs etc.

```html
<!DOCTYPE html>
<html lang="en">
<head>
<meta charset="utf-8">
<title>Briefly Ledger – Briefings</title>
<link href="https://fonts.googleapis.com/css2?family=Open+Sans:wght@400;600;700&display=swap" rel="stylesheet">
<style>
  :root{
    --blue:#2a8cc4;
    --blue-dark:#1f77a9;
    --ink:#333a40;
    --muted:#6a6f74;
    --panel:#f5f5f5;
    --line:#dedede;
    --field:#ffffff;
    --footer:#f7f7f7;
    --white:#ffffff;
  }
  *{box-sizing:border-box;margin:0;padding:0}
  html,body{width:1200px;height:896px;overflow:hidden;background:var(--white)}
  body{font-family:"Open Sans",Arial,sans-serif;color:var(--ink);position:relative}
  .page{position:relative;width:1200px;height:896px;overflow:hidden}

  .hero{position:absolute;left:0;top:0;width:1200px;height:258px;
    background:linear-gradient(180deg,#3b4f63 0%,#5a6470 28%,#2b3540 62%,#1a2027 100%)}
  .brand{position:absolute;left:97px;top:40px;width:314px;height:57px;background:var(--white);
    display:flex;align-items:center;justify-content:center;gap:12px}
  .brand-mark{width:22px;height:22px;border-radius:50%;background:var(--blue)}
  .brand-name{font-weight:700;font-size:30px;letter-spacing:.5px;color:var(--blue)}
  .sign-in{position:absolute;left:982px;top:52px;width:83px;height:32px;border:1px solid #8fcbea;border-radius:4px;
    background:var(--blue);color:var(--white);font-weight:700;font-size:13px;display:flex;align-items:center;justify-content:center}
  .menu{position:absolute;left:1079px;top:59px}

  .tabs{position:absolute;left:98px;top:296px;width:1002px;height:42px;border-bottom:1px solid var(--blue)}
  .tab{position:absolute;top:0;height:41px;display:flex;align-items:center;font-weight:600;font-size:15.5px;color:var(--ink);letter-spacing:.2px}
  .tab.press{left:32px}
  .tab.events{left:294px}
  .tab.briefings{left:436px;width:206px;justify-content:center;background:var(--blue);color:var(--white)}

  .panel{position:absolute;left:98px;top:338px;width:1002px;height:381px;background:var(--panel);border:1px solid #e4e4e4;border-top:none}
  .label{position:absolute;font-size:13.5px;color:var(--muted)}
  .field{position:absolute;width:348px;height:35px;background:var(--field);border:1px solid var(--line);border-radius:2px}
  .field::after{content:"";position:absolute;right:35px;top:0;bottom:0;border-left:1px solid #ececec}
  .field .value{position:absolute;left:12px;top:9px;font-size:11px;color:var(--muted)}
  .field .caret{position:absolute;right:12px;top:15px}
  .submit{position:absolute;left:50px;top:276px;width:127px;height:37px;background:var(--blue);color:var(--white);
    font-family:Arial,sans-serif;font-size:16px;display:flex;align-items:center;justify-content:center;border-radius:1px}

  .sources{position:absolute;left:426px;top:79px;width:347px;height:171px;background:var(--field);border:1px solid var(--line)}
  .sources-head{height:34px;border-bottom:1px solid var(--line);display:flex;align-items:center;padding-left:16px;font-size:11px;color:var(--muted);gap:12px;position:relative}
  .sources-head::after{content:"";position:absolute;right:35px;top:0;bottom:0;border-left:1px solid #ececec}
  .source-list{list-style:none;position:absolute;left:16px;top:50px}
  .source-list li{display:flex;align-items:center;gap:12px;height:23px;font-size:12px;color:var(--ink)}
  .box{width:11px;height:11px;border:1px solid #9a9a9a;border-radius:2px;background:#f1f1f1;position:relative}
  .box svg{position:absolute;left:1px;top:1px}
  .scroll{position:absolute;right:0;top:34px;width:18px;bottom:0;background:#f0f0f0}
  .thumb{position:absolute;left:4px;top:19px;width:11px;height:37px;background:#c4c4c4}

  .footer{position:absolute;left:0;top:785px;width:1200px;height:111px;background:var(--footer);border-top:1px solid #ececec}
  .footer-links{position:absolute;left:98px;top:36px;font-size:12.5px;font-weight:600;color:var(--blue);display:flex;gap:13px}
  .footer-links .sep{color:var(--ink);font-weight:400}
  .copyright{position:absolute;left:98px;top:64px;font-size:12.5px;color:var(--ink)}
  .social{position:absolute;left:927px;top:35px;display:flex;gap:8px}
  .social span{width:28px;height:28px;border-radius:50%;background:var(--blue)}
</style>
</head>
<body>
<div class="page">
  <header class="hero" role="img" aria-label="Evening aerial photograph of a dense city skyline with high-rise towers">
  </header>
  <div class="brand"><span class="brand-mark"></span><span class="brand-name">BRIEFLY LEDGER</span></div>
  <div class="sign-in">SIGN IN</div>
  <svg class="menu" width="22" height="20" viewBox="0 0 22 20" aria-hidden="true">
    <rect y="0" width="22" height="4" fill="#fff"/><rect y="8" width="22" height="4" fill="#fff"/><rect y="16" width="22" height="4" fill="#fff"/>
  </svg>

  <nav class="tabs">
    <div class="tab press">PRESS HEADLINES</div>
    <div class="tab events">EVENTS</div>
    <div class="tab briefings">BRIEFINGS</div>
  </nav>

  <section class="panel">
    <div class="label" style="left:49px;top:58px">Daily briefings :</div>
    <div class="field" style="left:49px;top:79px"></div>
    <div class="label" style="left:49px;top:126px">Driefing Date :</div>
    <div class="field" style="left:49px;top:148px"></div>
    <div class="label" style="left:49px;top:195px">Daily Press Briefing :</div>
    <div class="field" style="left:49px;top:216px">
      <span class="value">Past 24 hours</span>
      <svg class="caret" width="10" height="6" viewBox="0 0 10 6"><path d="M0 0h10L5 6z" fill="#555"/></svg>
    </div>
    <div class="submit">SUBMIT</div>

    <div class="label" style="left:426px;top:58px">Today's Briefing :</div>
    <div class="sources">
      <div class="sources-head"><span class="box"><svg width="9" height="9" viewBox="0 0 9 9"><path d="M1 4.5l2.2 2.3L8 1.5" stroke="#333" stroke-width="1.6" fill="none"/></svg></span>All Sources</div>
      <ul class="source-list">
        <li><span class="box"><svg width="9" height="9" viewBox="0 0 9 9"><path d="M1 4.5l2.2 2.3L8 1.5" stroke="#333" stroke-width="1.6" fill="none"/></svg></span>United Kingdom</li>
        <li><span class="box"><svg width="9" height="9" viewBox="0 0 9 9"><path d="M1 4.5l2.2 2.3L8 1.5" stroke="#333" stroke-width="1.6" fill="none"/></svg></span>Iraq</li>
        <li><span class="box"><svg width="9" height="9" viewBox="0 0 9 9"><path d="M1 4.5l2.2 2.3L8 1.5" stroke="#333" stroke-width="1.6" fill="none"/></svg></span>Bahrain/region</li>
        <li><span class="box"><svg width="9" height="9" viewBox="0 0 9 9"><path d="M1 4.5l2.2 2.3L8 1.5" stroke="#333" stroke-width="1.6" fill="none"/></svg></span>Syria/region</li>
        <li><span class="box"><svg width="9" height="9" viewBox="0 0 9 9"><path d="M1 4.5l2.2 2.3L8 1.5" stroke="#333" stroke-width="1.6" fill="none"/></svg></span>Counterterrorism/iran</li>
      </ul>
      <div class="scroll">
        <svg style="position:absolute;left:5px;top:5px" width="8" height="5" viewBox="0 0 8 5"><path d="M0 5h8L4 0z" fill="#777"/></svg>
        <div class="thumb"></div>
        <svg style="position:absolute;left:5px;bottom:6px" width="8" height="5" viewBox="0 0 8 5"><path d="M0 0h8L4 5z" fill="#777"/></svg>
      </div>
    </div>
  </section>

  <footer class="footer">
    <div class="footer-links"><span>ABOUT US</span><span class="sep">/</span><span>PRESS</span><span class="sep">/</span><span>CONTACT US</span></div>
    <div class="copyright">2016 © Copyrights BRIEFLY ledger.All Rights Reserved</div>
    <div class="social" aria-label="Social links"><span></span><span></span><span></span><span></span><span></span></div>
  </footer>
</div>
</body>
</html>
```